Community coffee table book/quiz book

I need a couple of things for my book:
- Book cover (Title: "1000 spørsmål om Kvernhaugen")
- "Cover pages" for each chapter of the book (15-16 chapters)
- "Watermark" or background design for all the pages of the book.
- A cover image for the book's Kretsbok page.
- Design of a paper "belt"

The book:
The book will consist of about 200+ pages with ten questions on one page and ten answers on the next.

The name of the book is "1000 spørsmål om Kvernhaugen" which means 1000 questions about Fyllingsdalen (Fyllingsdalen is a suburb of the city Bergen in Norway). Author is Helge Myrvold.
The questions in the book are grouped in chapters like:
History
Facts
Schools
Businesses
People/profiles
Sport
Culture
Buildings/Landmarks/Sculptures
The different areas of the suburb
The city
Language/expressions
Nature
The names of the chapters are not set, so it would be good to have the option to change the title of the pages without having to contact the designer (maybe by adding the text on top of the cover page?). I therefore suggest that these images are without text.
The book size is 18X18 cm.

The chapter cover pages:
The book will basically consist of text. Ten questions on one page, and ten questions on the next. Visually it will be quite "boring" to look at. I would therefore like to have a chapter cover page for each chapter, preferable in colour.

Water mark:
To avoid having a book full of white pages with limited amount of text I thought of having some kind of design on each page. I do not know how this should be done, but maybe it is possible to create some kind of background image or watermark image with similar design as the book cover and the chapter covers?

The Kretsbok cover image:
This should be the same as, or similar to, the book cover.
I believe the optimal size is 828px x 315px?

Paper "belt":
The book is to be sold for charity. The receiver of the money is the local sports club. I would like to have the book "wrapped in a 5-6 cm wide paper belt with the logo of the sports club (please see logo and colours here: http://www.ilbrattlia.no). I do not think that the book cover itself should have the sports club's color (purple), but maybe the paper band could? (Again: YOU are the designer)

Photos:
I reckon you would like some photos for both the book cover and the chapter covers. I will of course do the best I can to provide these photos when I have selected a designer. I the meantime

Target Market(s)

Target market is middle clas men and women 35+ from the geographical area Fyllingsdalen.

Industry/Entity Type

Community

Font styles to use
Serif
Sans Serif

Requirements
Must have
• The book will be sold by children on doors. The buyers will probably take a look briefly through the book and then decide if they are going to buy.
• It is important that they like the question types, categories and some of the actual questions they read. But it is also important that they like the look of the book. Therefore the book cover and the chapter cover pages must be appealing enough for the buyers to want this book on theor coffee table.
Nice to have
• I have uploaded a short video clip to Vidtrekk (https://www.vidtrekk.example/watch?v=qx7Ta2Lm9pz). This a promo clip from Pimlo Kanalen. I felt inspired when I saw it and thought that backgrounds like the ones used in the promo could also be used as backgrounds for each chapter's cover pages. Maybe different colour for each chapter? Screenshots from the clip is uploaded below.
• Then again: Maybe I am an idiot? YOU are the designer :-)
Should not have
• There has been some rivalry between two sportsclubs in the region after the clubs was merged a couple of years ago. I therefore believe we should therefore try avoid both the old clubs' colours (blue&yellow and green) and the new club's colour (purple).

```html
<!DOCTYPE html>
<html lang="en">
<head>
<meta charset="utf-8">
<title>Chapter Cover Pages</title>
<link rel="stylesheet" href="https://fonts.googleapis.com/css2?family=Bebas+Neue&family=Pacifico&family=PT+Sans+Narrow&display=swap">
<style>
  :root {
    --page-bg: #ffffff;
    --gold: #c49a10;
    --gold-light: #d2a917;
    --board-dark: #2a2828;
    --board-mid: #363331;
    --board-light: #3f3b37;
    --outline-title: #f1dcd2;
    --script-title: #f6c400;
    --ornament-white: #e9e6e2;
    --label-ink: #111111;
  }
  * { margin: 0; padding: 0; box-sizing: border-box; }
  html, body {
    width: 1200px;
    height: 1000px;
    overflow: hidden;
    background: var(--page-bg);
  }
  .sheet {
    position: relative;
    width: 1200px;
    height: 1000px;
  }
  .chapter-cover {
    position: absolute;
    top: 214px;
    width: 511px;
    height: 511px;
    background: var(--gold);
  }
  .chapter-cover--history { left: 64px; }
  .chapter-cover--culture { left: 655px; }
  .chapter-cover__board {
    position: absolute;
    inset: 0;
    width: 511px;
    height: 511px;
    display: block;
  }
  .chapter-cover__dots {
    position: absolute;
    left: 152px;
    top: 205px;
    width: 185px;
    height: 6px;
    background: radial-gradient(circle, var(--ornament-white) 2.4px, transparent 2.8px) 0 0 / 16.8px 6px repeat-x;
  }
  .chapter-cover__title {
    position: absolute;
    left: 0;
    width: 511px;
    text-align: center;
    line-height: 1;
  }
  .chapter-cover__title--outline {
    top: 216px;
    font-family: "Bebas Neue", "Arial Narrow", sans-serif;
    font-size: 82px;
    letter-spacing: 2px;
    color: transparent;
    -webkit-text-stroke: 1.3px var(--outline-title);
  }
  .chapter-cover__title--script {
    top: 196px;
    font-family: "Pacifico", cursive;
    font-size: 58px;
    color: var(--script-title);
  }
  .chapter-cover__divider {
    position: absolute;
    left: 111px;
    top: 295px;
    width: 282px;
    height: 4px;
    border-radius: 2px;
    background: linear-gradient(90deg, transparent, var(--ornament-white) 20%, var(--ornament-white) 80%, transparent);
    opacity: 0.85;
  }
  .sheet__label {
    position: absolute;
    top: 814px;
    left: 0;
    width: 1200px;
    text-align: center;
    font-family: "PT Sans Narrow", "Arial Narrow", sans-serif;
    font-size: 46px;
    color: var(--label-ink);
    letter-spacing: 0.5px;
  }
</style>
</head>
<body>
<main class="sheet">

  <section class="chapter-cover chapter-cover--history">
    <svg class="chapter-cover__board" viewBox="0 0 511 511" role="img" aria-label="Chalkboard texture background framed by gold corners">
      <defs>
        <linearGradient id="board-history" x1="0" y1="0" x2="1" y2="1">
          <stop offset="0" stop-color="var(--board-mid)"/>
          <stop offset="0.45" stop-color="var(--board-dark)"/>
          <stop offset="0.75" stop-color="var(--board-light)"/>
          <stop offset="1" stop-color="var(--board-dark)"/>
        </linearGradient>
      </defs>
      <path d="M0,91 Q210,-18 511,32 L511,420 Q330,535 0,478 Z" fill="url(#board-history)"/>
    </svg>
    <div class="chapter-cover__dots" role="img" aria-label="Row of dots ornament"></div>
    <h2 class="chapter-cover__title chapter-cover__title--outline">HISTORY</h2>
    <div class="chapter-cover__divider" role="img" aria-label="Decorative flourish divider"></div>
  </section>

  <section class="chapter-cover chapter-cover--culture">
    <svg class="chapter-cover__board" viewBox="0 0 511 511" role="img" aria-label="Chalkboard texture background framed by gold corners">
      <defs>
        <linearGradient id="board-culture" x1="0" y1="0" x2="1" y2="1">
          <stop offset="0" stop-color="var(--board-mid)"/>
          <stop offset="0.45" stop-color="var(--board-dark)"/>
          <stop offset="0.75" stop-color="var(--board-light)"/>
          <stop offset="1" stop-color="var(--board-dark)"/>
        </linearGradient>
      </defs>
      <path d="M0,91 Q210,-18 511,32 L511,420 Q330,535 0,478 Z" fill="url(#board-culture)"/>
    </svg>
    <h2 class="chapter-cover__title chapter-cover__title--script">Culture</h2>
    <div class="chapter-cover__divider" role="img" aria-label="Decorative flourish divider"></div>
  </section>

  <p class="sheet__label">COVER PAGES</p>
</main>
</body>
</html>
```